Website for Torvel Capital - investment banking firm

We have a corporate identity (thanks to Ravinka/31842) and want to extend that into a website design.  See the attached zipped files.
We have software folks in-house to do the coding.
See the attached Project Brief & Notes for more details.  Don't worry about the actual text - lorem ipsum will be fine.
The server will be Apache.
Thank you!
Desmond

Industry/Entity Type
Investment

```html
<!DOCTYPE html>
<html lang="en">
<head>
<meta charset="utf-8">
<title>Torvel Capital – Private Investment Banking</title>
<link href="https://fonts.googleapis.com/css2?family=Lato:ital,wght@0,400;0,700;1,400&family=Tinos&family=Montserrat:wght@400;500&display=swap" rel="stylesheet">
<style>
:root{
  --navy:#1f4e8f;
  --navy-dark:#173f77;
  --ink:#222;
  --grey:#555;
  --white:#fff;
}
*{box-sizing:border-box;margin:0;padding:0}
html,body{width:1200px;height:971px;overflow:hidden}
body{position:relative;font-family:"Lato",sans-serif;color:var(--ink);background:#fff}
.abs{position:absolute}

.hero-photo{left:0;top:94px;width:1200px;height:732px;
  background:linear-gradient(100deg,#c9d3dc 0%,#aab8c4 25%,#8d9aa6 45%,#5b6a7d 62%,#2f3a4f 72%,#7b8ea3 86%,#c0ccd6 100%)}
.lower-wash{left:0;top:540px;width:1200px;height:286px;
  background:linear-gradient(180deg,rgba(255,255,255,.72),rgba(255,255,255,.88))}

.site-header{left:0;top:0;width:1200px;height:94px;background:rgba(255,255,255,.96)}
.brand{left:132px;top:24px;display:flex;align-items:center;gap:14px}
.brand-mark{width:44px;height:44px;background:var(--navy)}
.brand-name{font-family:"Tinos",serif;font-size:34px;color:var(--navy);letter-spacing:.5px}

.contact-top{top:10px;display:flex;align-items:center;gap:8px;color:var(--navy)}
.contact-top svg{stroke:#444;fill:none;stroke-width:1.4}
.email-top{left:719px;font-size:13px}
.phone-top{left:901px;font-family:"Montserrat",sans-serif;font-size:19px;font-weight:500}

.main-nav{left:498px;top:57px;display:flex;align-items:center;font-size:14.5px;color:var(--ink)}
.main-nav a{color:inherit;text-decoration:none;padding:0 13px;line-height:16px;border-left:1px solid #999}
.main-nav a:first-child{border:none}
.main-nav a.active{background:var(--navy);color:#fff;line-height:26px;padding:0 16px}
.main-nav a.active + a{border-left:none}

.intro{left:131px;top:218px;width:463px;height:187px;background:rgba(255,255,255,.82)}
.intro h1{position:absolute;left:27px;top:9px;font-family:"Tinos",serif;font-weight:400;font-size:33px;color:var(--navy);white-space:nowrap}
.intro p{position:absolute;left:26px;font-family:"Montserrat",sans-serif;color:var(--ink);white-space:nowrap}
.intro .sub{top:54px;font-size:15px}
.intro .caps{top:84px;font-size:16.5px;font-weight:500;letter-spacing:.2px}
.cta{position:absolute;left:27px;top:122px;width:178px;height:46px;color:#fff;font-size:18px}
.cta span{position:absolute;left:16px;top:11px;white-space:nowrap}

.card{top:527px;width:288px;height:163px;background:linear-gradient(180deg,rgba(255,255,255,.9),rgba(255,255,255,.97));border-radius:4px 4px 0 0}
.card h2{position:absolute;left:16px;top:6px;font-family:"Tinos",serif;font-weight:400;font-size:25px;color:var(--ink);white-space:nowrap}
.card h2 em{font-style:normal;color:var(--navy)}
.card .icon{position:absolute;left:15px;top:53px}
.card .body{position:absolute;left:89px;top:52px;width:195px;font-size:13px;line-height:19.7px;color:#333;white-space:nowrap}
.card .more{position:absolute;left:89px;top:139px;font-size:11.5px;font-weight:700;color:var(--navy)}
.who .body{letter-spacing:.6px}
.services{list-style:none}
.services li{position:relative;padding-left:13px;line-height:16px;margin-bottom:6px}
.services li::before{content:"";position:absolute;left:0;top:4px;border-left:5px solid #888;border-top:4px solid transparent;border-bottom:4px solid transparent}
.news strong{display:block;font-weight:700;color:var(--ink)}

.divider{left:172px;top:705px;width:860px;height:1px;background:linear-gradient(90deg,transparent,#bbb 20%,#bbb 80%,transparent)}
.testi-title{left:143px;top:729px;width:125px;text-align:right;font-family:"Tinos",serif;font-size:26px;line-height:30px;font-weight:400}
.testi-title em{font-style:normal;color:var(--navy)}
.quote{left:339px;top:734px;width:730px;font-style:italic;font-size:13.6px;line-height:20px;color:#333;white-space:nowrap}
.quote .mark{font-family:"Tinos",serif;font-size:30px;color:#999;line-height:0;vertical-align:-10px;font-style:normal}
.quote-by{left:339px;top:781px;font-style:italic;font-size:13.6px;color:var(--navy)}

.site-footer{left:0;top:826px;width:1200px;height:145px;background:var(--navy);color:#fff}
.site-footer h3{position:absolute;top:14px;font-size:17.5px;font-weight:700}
.rule{position:absolute;top:43px;height:1px;background:rgba(255,255,255,.35)}
.addr{position:absolute;left:156px;top:55px;font-size:12.5px;line-height:19.5px}
.foot-line{position:absolute;left:338px;display:flex;align-items:center;gap:14px;font-weight:700}
.foot-line svg{stroke:#cfd9e8;fill:none;stroke-width:1.3}
.newsletter{position:absolute;left:554px;top:59px;width:245px;height:28px;display:flex}
.newsletter .field{flex:1;background:var(--navy-dark);font-style:italic;font-size:12px;color:#a9b9d2;padding:7px 10px}
.newsletter .go{width:37px;background:#fff;color:var(--navy);font-weight:700;font-size:15px;text-align:center;line-height:28px}
.follow{position:absolute;left:554px;top:103px;display:flex;align-items:center;gap:9px;font-weight:700;font-size:15.5px}
.follow .dot{width:29px;height:29px;border:1.5px solid #fff;border-radius:50%}
.badge{position:absolute;left:917px;top:-26px;width:106px;height:80px;border-radius:0 0 53px 53px;background:#fff;display:flex;align-items:center;justify-content:center}
.badge i{width:56px;height:56px;border-radius:50%;border:2px solid var(--navy)}
.copy{position:absolute;left:870px;top:77px;width:200px;text-align:center;font-size:13.5px;line-height:19px}
</style>
</head>
<body>

<div class="abs hero-photo" role="img" aria-label="Photograph of a businessman in a suit gazing over a harbour with cranes and glass office towers"></div>
<div class="abs lower-wash"></div>

<header class="abs site-header">
  <div class="abs brand"><span class="brand-mark"></span><span class="brand-name">TORVEL CAPITAL</span></div>

  <div class="abs contact-top email-top">
    <svg width="31" height="24" viewBox="0 0 31 24"><rect x="1" y="1" width="24" height="22" rx="3"/><path d="M25 9l5 3-5 3M6 8h14v9H6zM6 8l7 5 7-5"/></svg>
    info@torvelcapital.com
  </div>
  <div class="abs contact-top phone-top">
    <svg width="31" height="24" viewBox="0 0 31 24"><rect x="1" y="1" width="24" height="22" rx="3"/><path d="M25 9l5 3-5 3M10 5h6v14h-6zM11 8h4"/></svg>
    469-555-0148
  </div>

  <nav class="abs main-nav">
    <a class="active">About</a><a>Services</a><a>Current Engagements</a><a>Completed Transactions</a><a>Contact Us</a>
  </nav>
</header>

<section class="abs intro">
  <h1>Private Investment Banking</h1>
  <p class="sub">advisory firm that acts as an intermediary on behalf of</p>
  <p class="caps">BUYERS &amp; SELLERS OF PRIVATE COMPANIES.</p>
  <div class="cta">
    <svg width="178" height="46" viewBox="0 0 178 46"><path d="M0 0h160l18 23-18 23H0z" fill="#1f4e8f"/></svg>
    <span>Get Started Now</span>
  </div>
</section>

<article class="abs card who" style="left:134px">
  <h2><em>Who</em> We Are</h2>
  <svg class="icon" width="60" height="60" viewBox="0 0 60 60"><circle cx="30" cy="30" r="28" fill="#fff" stroke="#333" stroke-width="2"/><circle cx="30" cy="24" r="7" fill="#333"/><path d="M17 43c2-9 24-9 26 0z" fill="#333"/></svg>
  <p class="body">Torvel Capital's history in<br>mergers and acquisitions<br>traces back to 1998. We pride<br>our selves in successfully</p>
  <a class="more">READ MORE »</a>
</article>

<article class="abs card what" style="left:456px">
  <h2><em>What</em> We Do</h2>
  <svg class="icon" width="60" height="60" viewBox="0 0 60 60"><circle cx="30" cy="30" r="28" fill="#fff" stroke="#333" stroke-width="2"/><circle cx="26" cy="34" r="8" fill="none" stroke="#333" stroke-width="5"/><circle cx="39" cy="21" r="5" fill="none" stroke="#333" stroke-width="4"/></svg>
  <ul class="body services">
    <li>Buy-Side Acquisitions</li>
    <li>Recapitalizations &amp; Growth<br>Capital Partnerships</li>
    <li>Sell-Side Transactions</li>
  </ul>
  <a class="more">READ MORE »</a>
</article>

<article class="abs card news" style="left:778px">
  <h2><em>Latest</em> News</h2>
  <svg class="icon" width="60" height="60" viewBox="0 0 60 60"><circle cx="30" cy="30" r="28" fill="#fff" stroke="#333" stroke-width="2"/><path d="M16 25h7l15-9v28l-15-9h-7z" fill="#333"/><rect x="19" y="35" width="5" height="9" fill="#333"/></svg>
  <div class="body"><strong>Kauitm veleum iriure lorrfu</strong>Hdrehrit in vulptate velit essehi<br>molestie coequa. molestie uitmi<br>veleum iriure lorrfu hdrehrit</div>
  <a class="more">READ MORE »</a>
</article>

<div class="abs divider"></div>
<h2 class="abs testi-title"><em>Client</em><br>Testimonials</h2>
<blockquote class="abs quote"><span class="mark">“</span> Lorem ipsum sit amet consectet uradi incididunt ut labore et dolore magna aliquaps enimi ad minim veniam quiidunt<br>ut labore etpvloore magn incididunt ut labore et dolore na aliquatmp enimt ad minim veniam quiidunt ut labore <span class="mark">”</span></blockquote>
<p class="abs quote-by">Mr. Dolore na Aliqua</p>

<footer class="abs site-footer">
  <h3 style="left:133px">Contact Info</h3>
  <div class="rule" style="left:133px;width:366px"></div>
  <svg class="abs" style="left:134px;top:59px" width="11" height="15" viewBox="0 0 11 15"><path d="M5.5 14C2 9 1 7.5 1 5.5a4.5 4.5 0 0 1 9 0C10 7.5 9 9 5.5 14z" fill="#cfd9e8"/><circle cx="5.5" cy="5.5" r="1.7" fill="#1f4e8f"/></svg>
  <p class="addr">Hong Kong: Suite 1804<br>Harbourline Tower<br>12 - 18 Marlowe Road<br>Kellston, Hong Kong</p>
  <div class="foot-line" style="top:55px;font-size:15px">
    <svg width="10" height="16" viewBox="0 0 10 16"><rect x="1" y="1" width="8" height="14" rx="1.5"/><path d="M3 12h4"/></svg>469-555-0148
  </div>
  <div class="foot-line" style="top:89px;font-size:13px">
    <svg width="15" height="11" viewBox="0 0 15 11"><rect x="1" y="1" width="13" height="9"/><path d="M1 1l6.5 5 6.5-5"/></svg>info@torvelcapital.com
  </div>

  <h3 style="left:554px">Newsletter Signup</h3>
  <div class="rule" style="left:554px;width:241px"></div>
  <div class="newsletter"><span class="field">Enter your email</span><span class="go">GO</span></div>
  <div class="follow">Follow Us On: <span class="dot"></span><span class="dot"></span><span class="dot"></span><span class="dot"></span></div>

  <div class="badge"><i></i></div>
  <p class="copy">© Copyright 2014 Torvel Capital.<br>All Rights Reserved</p>
</footer>

</body>
</html>
```